Website Development for vaultmerrow.com.au

Build a new Wordpress/Responsive website for vaultmerrow.com.au

Target Market(s)

Compliance Managers, Risk Managers, Information Security and Cyber Security Professionals, Chief Data/Digital Officers, Chief Operating/Financial Officers, Business Continuity Professionals, Disaster Recovery Planners, Small Business Owners, Local/Federal Government entities

Industry/Entity Type

Data Service

Coding

Coded - Design and coding required

Number of Pages Required

5+ page

Font styles to use
Sans Serif

Colors

Designer to choose colors to be used in the design.

Requirements
Must have
• 1. Site Structure: Home Page plus the following chapter-pages for a) Services b) About c) Resources d) Blog e) Contact Us
• 2. Prefer site to built on wordpress and we can purchase a theme if needed (we currently use Kelp9 for other sites)
• 3. Blog needs to be wordpress based
• 4. We will host the site ourselves on our own servers
• 5. Responsive Design
Nice to have
• 1. Livechat capability/interface
• 2. Capability for marketing automation integration (such as hubspot, marketo, infusionsoft etc)
• 3. Capability for CRM integration (Salesforce)

```html
<!DOCTYPE html>
<html lang="en">
<head>
<meta charset="utf-8">
<title>Blog – Vaultmerrow</title>
<link rel="stylesheet" href="https://fonts.googleapis.com/css2?family=Roboto:wght@400;500;700&family=Mulish:wght@400;600;700&display=swap">
<style>
:root{
  --red:#e8202a;
  --red-dark:#8c0d14;
  --ink:#222;
  --body:#555;
  --grey-bar:#8b8b8d;
  --grey-foot:#6f6f72;
  --light:#f4f4f4;
  --line:#e3e3e3;
  --white:#fff;
  --black:#0c0c0c;
}
*{box-sizing:border-box;margin:0;padding:0}
html,body{width:1200px;height:2848px;overflow:hidden}
body{position:relative;background:var(--white);font-family:"Mulish",sans-serif;color:var(--body)}
.abs{position:absolute}
/* top bar */
.topbar{left:0;top:0;width:1200px;height:48px;background:var(--grey-bar);color:var(--white);font-size:14px;display:flex;align-items:center;padding:0 142px}
.topbar .contact{display:flex;gap:52px}
.topbar .contact span{display:flex;align-items:center;gap:10px}
.topbar .follow{margin-left:auto;display:flex;align-items:center;gap:6px;font-family:"Roboto",sans-serif;font-weight:700}
.topbar .follow i{display:inline-block;width:20px;height:20px;border-radius:2px;background:var(--red)}
.topbar .follow i.b{background:#2aa3e0}.topbar .follow i.c{background:#1b6fa5}
/* nav */
.nav{left:0;top:48px;width:1200px;height:82px;background:#f7f7f7;display:flex;align-items:center;padding:0 142px}
.brand{display:flex;align-items:center;gap:10px;font-family:"Roboto",sans-serif;font-weight:700;font-size:32px;color:var(--red)}
.brand b{width:26px;height:26px;border-radius:50%;background:var(--red);display:block}
.nav ul{margin-left:auto;display:flex;gap:30px;list-style:none;font-family:"Roboto",sans-serif;font-size:15px;color:var(--ink)}
.nav li.active{color:var(--red);position:relative}
.nav li.active:before{content:"";position:absolute;left:-6px;right:-6px;top:-36px;height:4px;background:var(--red)}
.nav li.active:after{content:"";position:absolute;left:-6px;right:-6px;bottom:-36px;height:4px;background:var(--red)}
/* hero */
.hero{left:0;top:130px;width:1200px;height:392px;background:var(--light);overflow:hidden}
.hero-photo{position:absolute;inset:0 0 42px 0;background:radial-gradient(circle at 78% 45%,#ff4b55 0,#c4121c 22%,#7d0a10 48%,#3a0508 100%)}
.hero-curve{position:absolute;left:0;bottom:0;width:1200px;height:250px}
.hero h1{position:absolute;left:142px;top:52px;font-family:"Roboto",sans-serif;font-weight:400;font-size:42px;line-height:54px;color:var(--white);letter-spacing:.5px}
.hero h1 strong{font-weight:700}
.hero h1 small{display:block;font-size:28px;line-height:40px}
.crumbs{position:absolute;left:142px;top:363px;font-family:"Roboto",sans-serif;font-size:14px;color:var(--ink)}
.crumbs em{font-style:normal;color:var(--red);font-weight:700}
.page-title{left:0;top:592px;width:1200px;text-align:center;font-family:"Roboto",sans-serif;font-weight:500;font-size:38px;color:var(--ink)}
/* article */
.post{left:142px;top:691px;width:603px}
.post-photo{width:603px;height:382px;background:linear-gradient(160deg,#4a4a48,#1d1d1f 60%,#2b3340);position:relative}
.date{position:absolute;left:4px;top:0;width:38px;background:var(--red);color:var(--white);font-family:"Roboto",sans-serif;font-size:13px;text-align:center;line-height:18px;padding:2px 0 4px}
.date b{display:block;font-size:18px}
.post h2{font-family:"Roboto",sans-serif;font-weight:400;font-size:15px;color:var(--ink);margin-top:20px}
.meta{font-size:11px;margin-top:10px;color:var(--body)}
.meta .k{color:var(--red);font-weight:700;margin-right:8px}
.tags{display:flex;font-size:10px;line-height:16px;margin-top:8px}
.tags .k{color:var(--red);font-weight:700;margin-right:8px;font-size:11px}
.post p{font-size:12px;line-height:20px;text-align:justify;margin-top:14px}
.share{font-family:"Roboto",sans-serif;font-size:14px;color:var(--ink);margin-top:16px;display:flex;align-items:center;gap:6px}
.rule{border-top:1px solid var(--line);margin-top:22px}
.sec-h{font-family:"Roboto",sans-serif;font-size:15px;color:var(--ink);margin-top:20px}
.comment{margin-left:16px;margin-top:10px;font-size:11px}
.comment .who{color:var(--red);font-size:12px}
.comment .when{color:var(--ink);margin-top:6px;font-size:10px}
.comment p{margin-top:6px;font-size:11px;line-height:19px;text-align:left}
.pill{display:inline-flex;align-items:center;height:34px;width:128px;border-radius:17px;background:var(--black);color:var(--white);font-family:"Roboto",sans-serif;font-size:14px;position:relative;padding-left:58px}
.pill:before{content:"";position:absolute;left:0;top:2px;width:30px;height:30px;border-radius:50%;background:var(--white);border:3px solid var(--black)}
.form{margin-left:16px;display:grid;grid-template-columns:288px 288px;column-gap:14px;margin-top:10px}
.form label{display:block;font-size:10px;color:var(--ink);margin-bottom:6px}
.form label i{color:var(--red);font-style:normal}
.form .box{height:34px;border:1px solid var(--line);margin-bottom:18px}
.form .full{grid-column:1/3}
.form .area{height:64px}
/* sidebar */
.side{left:771px;top:691px;width:287px}
.search{display:flex;height:38px}
.search div{flex:1;background:#f2f2f2;font-size:11px;color:#666;padding:12px 16px}
.search span{width:42px;background:var(--red);display:flex;align-items:center;justify-content:center}
.widget{border:1px solid var(--line);margin-top:31px}
.widget h3{background:var(--red);color:var(--white);font-family:"Roboto",sans-serif;font-weight:500;font-size:18px;height:35px;line-height:35px;padding-left:16px}
.widget ul{list-style:none;padding:6px 18px 0 20px}
.widget li{font-size:12px;color:var(--ink);height:38px;display:flex;align-items:center;border-bottom:1px solid var(--line)}
.widget li:last-child{border-bottom:0}
.widget li:before{content:"»";margin-right:8px;font-size:13px}
.widget li span{margin-left:auto}
.tabs{display:flex;gap:10px;padding:15px 18px 0 20px}
.tabs div{height:27px;line-height:27px;padding:0 16px;background:#8e8e90;color:var(--white);font-size:11px;position:relative}
.tabs .on{background:var(--red)}
.tabs .on:after{content:"";position:absolute;left:50%;bottom:-6px;margin-left:-6px;border:6px solid transparent;border-bottom:0;border-top-color:var(--red)}
/* cta */
.cta{left:0;top:2203px;width:1200px;height:469px;background:linear-gradient(135deg,#e9353d,#d8232b 50%,#e24048);text-align:center}
.cta h2{margin-top:102px;font-family:"Roboto",sans-serif;font-weight:500;font-size:38px;color:var(--white)}
.cta-form{position:absolute;left:313px;top:188px;width:642px;height:139px;border:1px solid rgba(255,255,255,.55);display:grid;grid-template-columns:322px 1fr;text-align:left;font-size:12px;color:rgba(255,255,255,.85)}
.cta-form .col{border-right:1px solid rgba(255,255,255,.55)}
.cta-form .col div{height:46px;line-height:46px;padding-left:18px;border-bottom:1px solid rgba(255,255,255,.55)}
.cta-form .col div:last-child{border-bottom:0}
.cta-form .msg{padding:18px 20px}
.cta .pill{position:absolute;left:537px;top:363px}
.chat{left:1016px;top:2643px;width:46px;height:46px;border-radius:50%;background:var(--white);box-shadow:0 2px 8px rgba(0,0,0,.3);display:flex;align-items:center;justify-content:center}
.chat:after{content:"";position:absolute;right:0;top:0;width:12px;height:12px;border-radius:50%;background:var(--red);border:2px solid var(--white)}
/* footer */
.footer{left:0;top:2672px;width:1200px;height:176px;background:var(--grey-foot);color:var(--white)}
.footer .brand{position:absolute;left:142px;top:58px;color:var(--white);font-size:40px}
.footer .brand b{background:var(--white)}
.footer ul{position:absolute;right:142px;top:74px;display:flex;gap:40px;list-style:none;font-family:"Roboto",sans-serif;font-size:13px}
.footer .base{position:absolute;left:142px;right:142px;top:133px;border-top:1px solid rgba(255,255,255,.25);padding-top:13px;display:flex;justify-content:space-between;font-size:11px}
</style>
</head>
<body>

<header class="topbar abs">
  <div class="contact">
    <span><svg width="16" height="16" viewBox="0 0 24 24" fill="none" stroke="#fff" stroke-width="2"><path d="M5 3h4l2 5-3 2a11 11 0 0 0 6 6l2-3 5 2v4a2 2 0 0 1-2 2A18 18 0 0 1 3 5a2 2 0 0 1 2-2z"/></svg>+012-555-019</span>
    <span><svg width="18" height="14" viewBox="0 0 24 18" fill="none" stroke="#fff" stroke-width="2"><rect x="1" y="1" width="22" height="16"/><path d="M1 1l11 9 11-9"/></svg>info@vaultmerrow.com.au</span>
  </div>
  <div class="follow">Follow Us on&nbsp;<i></i><i class="b"></i><i class="c"></i><i></i></div>
</header>

<nav class="nav abs">
  <div class="brand"><b></b>Vaultmerrow</div>
  <ul><li>HOME</li><li>ABOUT</li><li>SERVICES</li><li>RESOURCES</li><li class="active">BLOG</li><li>CONTACT US</li></ul>
</nav>

<section class="hero abs">
  <div class="hero-photo" role="img" aria-label="Red glowing globe of security icons held by a hand"></div>
  <svg class="hero-curve" viewBox="0 0 1200 250" preserveAspectRatio="none"><path d="M0 40 Q600 330 1200 110 L1200 250 L0 250Z" fill="#f4f4f4"/></svg>
  <h1>DELIVERING <strong>QUALITY</strong><br>SERVICES THROUGH<br><strong>INNOVATION</strong><small>From Industry&nbsp; Experts</small></h1>
  <div class="crumbs">HOME &nbsp;»&nbsp; BLOG &nbsp;»&nbsp; <em>LOREM IPSUM DOLOR SIT AMET...</em></div>
</section>

<h1 class="page-title abs">BLOG</h1>

<article class="post abs">
  <div class="post-photo" role="img" aria-label="Dark studio desk with three monitors and speakers">
    <div class="date">FEB<b>07</b></div>
  </div>
  <h2>Lorem ipsum dolor sit amet, consectetuer adipiscing elit, sed diam nonummy.</h2>
  <div class="meta"><span class="k">Posted By:</span>Admin &nbsp;|&nbsp; <span class="k">Category:</span>Lorem Ipsum is simply dummy</div>
  <div class="tags"><span class="k">Tags:</span><span>Lorem ipsum, dolor sit amet, consectetur adipiscing elit, sed do eiusmod, tempor incididunt, ut labore et dolore, magna aliqua, Ut enim ad minim veniam, quis nostrud exercitation ullamco.</span></div>
  <p>Lorem ipsum dolor sit amet, consectetur adipiscing elit, sed do eiusmod tempor incididunt ut labore et dolore magna aliqua. Ut enim ad minim veniam, quis nostrud exercitation ullamco laboris nisi ut aliquip ex ea commodo consequat. Duis aute irure dolor in reprehenderit in voluptate velit esse cillum dolore eu fugiat nulla pariatur. Excepteur sint occaecat cupidatat non proident, sunt in culpa qui officia deserunt mollit anim id est laborum.</p>
  <p>Sed ut perspiciatis unde omnis iste natus error sit voluptatem accusantium doloremque laudantium, totam rem aperiam, eaque ipsa quae ab illo inventore veritatis et quasi architecto beatae vitae dicta sunt explicabo. Nemo enim ipsam voluptatem quia voluptas sit aspernatur aut odit aut fugit, sed quia consequuntur magni dolores eos qui ratione voluptatem sequi nesciunt. Neque porro quisquam est, qui dolorem ipsum quia dolor sit amet, consectetur, adipisci velit, sed quia non numquam eius modi tempora incidunt ut labore et dolore magnam aliquam quaerat voluptatem. Ut enim ad minima veniam, quis nostrum exercitationem ullam corporis suscipit laboriosam, nisi ut aliquid ex ea commodi consequatur? Quis autem vel eum iure reprehenderit qui in ea voluptate velit esse quam nihil molestiae consequatur, vel illum qui dolorem eum fugiat quo voluptas nulla pariatur.</p>
  <div class="share"><svg width="12" height="12" viewBox="0 0 24 24" fill="#222"><circle cx="18" cy="5" r="3"/><circle cx="6" cy="12" r="3"/><circle cx="18" cy="19" r="3"/><path d="M8 11l8-5M8 13l8 5" stroke="#222" stroke-width="2"/></svg>Share It</div>
  <div class="rule"></div>
  <div class="sec-h">Comments</div>
  <div class="comment">
    <div class="who">Mr. Tom Hale</div>
    <div class="when">12 March, 2019 At 16:10 PM</div>
    <p>Lorem Ipsum is simply dummy text of the printing and typesetting industry. It is a long established fact that a reader will be distracted by the readable content of a page when looking at its layout.</p>
    <div class="pill" style="margin-top:12px">Reply</div>
  </div>
  <div class="rule" style="margin-top:18px"></div>
  <div class="sec-h" style="margin-top:26px">Leave A Reply</div>
  <div class="form">
    <div><label>Name <i>*</i></label><div class="box"></div></div>
    <div><label>Email <i>*</i></label><div class="box"></div></div>
    <div><label>Phone <i>*</i></label><div class="box"></div></div>
    <div><label>Website</label><div class="box"></div></div>
    <div class="full"><label>Comment <i>*</i></label><div class="box area" style="margin-bottom:12px"></div></div>
    <div><div class="pill">Submit</div></div>
  </div>
</article>

<aside class="side abs">
  <div class="search"><div>Search Blog</div><span><svg width="16" height="16" viewBox="0 0 24 24" fill="none" stroke="#fff" stroke-width="3"><circle cx="10" cy="10" r="7"/><path d="M15 15l7 7"/></svg></span></div>
  <div class="widget">
    <h3>Categories</h3>
    <ul>
      <li>Lorem Ipsum is simply dummy<span>(02)</span></li>
      <li>Lorem Ipsum is simply dummy<span>(08)</span></li>
      <li>Lorem Ipsum is simply dummy<span>(05)</span></li>
      <li>Lorem Ipsum is simply dummy<span>(11)</span></li>
      <li>Lorem Ipsum is simply dummy<span>(06)</span></li>
      <li>Lorem Ipsum is simply dummy<span>(18)</span></li>
      <li>Lorem Ipsum is simply dummy<span>(13)</span></li>
      <li>Lorem Ipsum is simply dummy<span>(20)</span></li>
    </ul>
  </div>
  <div class="widget">
    <h3>Posts</h3>
    <div class="tabs"><div class="on">Popular</div><div>Commented</div><div>Tags</div></div>
    <ul>
      <li>Lorem Ipsum is simply dummy...</li>
      <li>Lorem Ipsum is simply dummy...</li>
      <li>Lorem Ipsum is simply dummy...</li>
      <li>Lorem Ipsum is simply dummy...</li>
      <li>Lorem Ipsum is simply dummy...</li>
    </ul>
  </div>
</aside>

<section class="cta abs" role="img" aria-label="Team meeting around a table, tinted red">
  <h2>LET’S GET STARTED</h2>
  <div class="cta-form">
    <div class="col"><div>Your Name*</div><div>Your Email*</div><div>Your Contact Number*</div></div>
    <div class="msg">Your Message*</div>
  </div>
  <div class="pill">Submit</div>
</section>

<div class="chat abs"><svg width="22" height="16" viewBox="0 0 22 16"><rect x="1" y="1" width="20" height="12" rx="6" fill="#222"/><circle cx="7" cy="7" r="1.5" fill="#fff"/><circle cx="11" cy="7" r="1.5" fill="#fff"/><circle cx="15" cy="7" r="1.5" fill="#fff"/></svg></div>

<footer class="footer abs">
  <div class="brand"><b></b>Vaultmerrow</div>
  <ul><li>HOME</li><li>ABOUT</li><li>SERVICES</li><li>RESOURCES</li><li>BLOG</li><li>CONTACT US</li></ul>
  <div class="base"><span>Copyright 2019 @ Vaultmerrow. All Rights Reserved.</span><span>Terms of Services / Privacy Policy</span></div>
</footer>

</body>
</html>
```